Velmora Freightway Solutions Business cards

Would like a very unique design catchy but professional for business cards. Please use log provided.Marlon WellsCeo and Founder TransCon Logistix Solutions1-888-913-3225mwells@tlsolutionsus.comwww.tlsolutionsus.com

```html
<!DOCTYPE html>
<html lang="en">
<head>
<meta charset="utf-8">
<title>Velmora Freightway Solutions – Business Cards</title>
<link rel="stylesheet" href="https://fonts.googleapis.com/css2?family=Open+Sans:wght@400;600;700&family=Cinzel:wght@700&display=swap">
<style>
  :root {
    --brand-blue: #0b74bd;
    --brand-red: #e3202a;
    --paper: #ffffff;
    --ink: #1c1c1c;
    --stage: #ece6dc;
  }
  * { box-sizing: border-box; margin: 0; padding: 0; }
  html, body { width: 1200px; height: 895px; overflow: hidden; }
  body {
    background: var(--stage);
    font-family: "Open Sans", sans-serif;
    position: relative;
  }
  .card {
    position: absolute;
    left: 250px;
    width: 700px;
    height: 400px;
    border-radius: 26px;
    overflow: hidden;
    box-shadow: 0 6px 18px rgba(0,0,0,0.18);
  }
  .card--front { top: 30px; background: var(--brand-blue); }
  .card--back { top: 465px; background: var(--paper); }

  .wordmark {
    position: absolute;
    display: flex;
    align-items: center;
    gap: 14px;
    font-family: "Open Sans", sans-serif;
    font-weight: 700;
    text-transform: uppercase;
    letter-spacing: 2px;
    white-space: nowrap;
  }
  .wordmark__mark { width: 34px; height: 34px; flex: none; }
  .card--front .wordmark {
    left: 50%; top: 50%;
    transform: translate(-50%, -50%);
    font-size: 31px;
    color: var(--paper);
  }
  .card--front .wordmark__mark { background: var(--paper); }
  .card--back .wordmark {
    left: 50%; top: 70px;
    transform: translateX(-50%);
    font-size: 26px;
    color: var(--brand-blue);
  }
  .card--back .wordmark__mark { width: 28px; height: 28px; background: var(--brand-blue); }

  .person {
    position: absolute;
    left: 44px;
    top: 240px;
    color: var(--ink);
  }
  .person__name {
    font-family: "Cinzel", serif;
    font-weight: 700;
    font-size: 26px;
    color: var(--brand-red);
    letter-spacing: 1px;
    line-height: 1.1;
  }
  .person__role, .person__company {
    font-size: 17px;
    line-height: 1.35;
  }

  .divider {
    position: absolute;
    left: 390px;
    top: 160px;
    width: 2px;
    height: 84px;
    background: var(--ink);
  }
  .contact {
    position: absolute;
    left: 416px;
    top: 162px;
    list-style: none;
    font-size: 16px;
    color: var(--ink);
  }
  .contact__item {
    display: flex;
    align-items: center;
    gap: 10px;
    height: 27px;
  }
  .contact__icon { width: 15px; height: 15px; flex: none; }

  .bands { position: absolute; left: 0; bottom: 0; width: 700px; height: 70px; }
</style>
</head>
<body>

  <section class="card card--front" aria-label="Card front">
    <div class="wordmark">
      <span class="wordmark__mark"></span>
      <span class="wordmark__name">Velmora Freightway Solutions</span>
    </div>
  </section>

  <section class="card card--back" aria-label="Card back">
    <div class="wordmark">
      <span class="wordmark__mark"></span>
      <span class="wordmark__name">Velmora Freightway Solutions</span>
    </div>

    <div class="divider"></div>
    <ul class="contact">
      <li class="contact__item">
        <svg class="contact__icon" viewBox="0 0 16 16" aria-hidden="true">
          <path fill="#e3202a" d="M3.5 1.5l2.5 0 1 3.5-1.8 1.2c.8 1.8 2.2 3.2 4 4l1.2-1.8 3.5 1v2.5c0 1-1 1.8-2 1.6C6.2 12.8 3.2 9.8 1.9 4 1.7 3 2.5 1.5 3.5 1.5z"/>
        </svg>
        <span>1-888-470-6158</span>
      </li>
      <li class="contact__item">
        <svg class="contact__icon" viewBox="0 0 16 16" aria-hidden="true">
          <rect x="1" y="3" width="14" height="10" rx="1" fill="#e3202a"/>
          <path d="M1.5 3.8L8 9l6.5-5.2" stroke="#fff" stroke-width="1.3" fill="none"/>
        </svg>
        <span>dpike@vfwayroutes.com</span>
      </li>
      <li class="contact__item">
        <svg class="contact__icon" viewBox="0 0 16 16" aria-hidden="true">
          <circle cx="8" cy="8" r="6.5" fill="#e3202a"/>
          <path d="M1.5 8h13M8 1.5c-3 3.5-3 9.5 0 13M8 1.5c3 3.5 3 9.5 0 13" stroke="#fff" stroke-width="1" fill="none"/>
        </svg>
        <span>www.vfwayroutes.com</span>
      </li>
    </ul>

    <div class="person">
      <p class="person__name">Dorian Pike</p>
      <p class="person__role">Ceo and Founder</p>
      <p class="person__company">Velmora Freightway Solutions</p>
    </div>

    <svg class="bands" viewBox="0 0 700 70" aria-hidden="true">
      <rect x="0" y="48" width="440" height="22" fill="var(--brand-blue)"/>
      <polygon points="448,48 454,30 700,30 700,70 448,70" fill="var(--brand-red)"/>
      <polygon points="440,48 446,48 446,70 440,70" fill="var(--brand-blue)"/>
    </svg>
  </section>

</body>
</html>
```